New & Improved KIVORA Business Card

I would like a two sided business card one side dedicated to home automation (security camera installation, television & sound bar mounting (hidden wires optional) , sink installation, fireplace mounting, chandelier installation and one side dedicated to all electronic repairs, In ex: plume band repairs, computer, zTab, laptop repairs, Velofon's, Korvex and etc.. Using the colors on this flyer. The phone number &email I want on both sides is (555) 214-3907 & Tech@Kivora.help. SAME COLOR AS THE FLYER ATTACHED.

Target Market(s)

EVERYONE.

Contact Information for Business Card

I would like a two sided business card one side dedicated to home automation (security camera installation, television & sound bar mounting (hidden wires optional) , sink installation, fireplace mounting, chandelier installation and one side dedicated to all electronic repairs, In ex: plume band repairs, computer, zTab, laptop repairs, Velofon's, Korvex and etc.. Using the colors on this flyer. The phone number &email I want on both sides is (555) 214-3907 & Tech@Kivora.help

Requirements
Must have
• -TV MOUNTING
-HOME AUTOMATION
-SECURITY CAMERA INSTALLATION
-ALL ELECTRONIC REPAIRS
- (555) 214-3907
-Tech@Kivora.help
-SAME COLOR AS THE FLYER
Nice to have
• Same colors & concept as the flyer attached below.
Should not have
• DO NOT DO A DIFF COLOR I WANT SAME COLOR AS THE FLYER ATTACHED.

```html
<!DOCTYPE html>
<html lang="en">
<head>
<meta charset="utf-8">
<title>Kivora Business Card</title>
<link rel="stylesheet" href="https://fonts.googleapis.com/css2?family=Roboto+Condensed:wght@400;500;700&family=Roboto:wght@400;500&display=swap">
<style>
  :root {
    --pink: #e8489a;
    --pink-light: #f06bb0;
    --pink-deep: #d8358a;
    --dark: #1c1c1c;
    --dark-2: #333333;
    --white: #ffffff;
    --paper: #f3f3f3;
    --ink: #151515;
    --stage: #e4e4e6;
  }
  * { margin: 0; padding: 0; box-sizing: border-box; }
  html, body { width: 1200px; height: 977px; overflow: hidden; }
  body {
    background: var(--stage);
    position: relative;
    font-family: "Roboto Condensed", "Arial Narrow", sans-serif;
  }
  .card {
    position: absolute;
    top: 155px;
    width: 377px;
    height: 667px;
    overflow: hidden;
    box-shadow: 0 6px 18px rgba(0,0,0,.18);
  }
  .card--repairs { left: 205px; background: var(--paper); }
  .card--automation { left: 618px; background: var(--dark); }
  .card__bg { position: absolute; inset: 0; width: 100%; height: 100%; }
  .logo {
    position: absolute; left: 0; right: 0;
    text-align: center;
    font-weight: 500;
    letter-spacing: 8px;
  }
  .card--repairs .logo { top: 140px; font-size: 30px; color: var(--white); }
  .card--automation .logo { top: 60px; font-size: 40px; color: var(--pink); }
  .categories {
    position: absolute; top: 208px; left: 26px; right: 26px;
    display: flex; justify-content: space-between;
    font-size: 10px; letter-spacing: 1px; color: rgba(255,255,255,.55);
  }
  .devices {
    position: absolute; top: 360px; left: 40px; width: 297px; height: 78px;
    background: linear-gradient(180deg, #cfcfd2, #2a2a2a);
    border-radius: 4px;
  }
  .tagline {
    position: absolute; top: 460px; left: 0; right: 0;
    text-align: center; font-weight: 700; font-size: 19px; line-height: 27px;
    color: var(--ink);
  }
  .headline {
    position: absolute; top: 524px; left: 0; right: 0;
    text-align: center; font-weight: 700; font-size: 22px; color: var(--pink);
  }
  .phone-pill {
    position: absolute; top: 570px; left: 15px; width: 347px; height: 33px;
    border-radius: 17px;
    background: linear-gradient(90deg, #050505, #3a3a3a 50%, #050505);
    display: flex; align-items: center; justify-content: center; gap: 6px;
    color: var(--pink); font-weight: 700; font-size: 19px;
  }
  .email {
    position: absolute; top: 616px; left: 0; right: 0;
    display: flex; align-items: center; justify-content: center; gap: 8px;
    font-family: "Roboto", sans-serif; font-size: 16px; color: var(--ink);
  }
  .section-title {
    position: absolute; top: 118px; left: 0; right: 0;
    text-align: center; font-weight: 700; font-size: 21px; color: var(--white);
  }
  .services {
    position: absolute; top: 190px; left: 30px; right: 20px;
    list-style: none;
    font-family: "Roboto", sans-serif; font-size: 17px; color: var(--white);
  }
  .services li {
    position: relative; padding-left: 28px; margin-bottom: 20px; line-height: 21px;
  }
  .services li::before {
    content: ""; position: absolute; left: 0; top: 3px;
    width: 14px; height: 14px; border-radius: 50%; background: var(--pink);
  }
  .services li::after {
    content: ""; position: absolute; left: 4px; top: 7px;
    width: 4px; height: 4px;
    border-top: 2px solid var(--white); border-right: 2px solid var(--white);
    transform: rotate(45deg);
  }
  .services .note { display: block; font-size: 15px; }
  .feature-pill {
    position: absolute; top: 445px; left: 15px; width: 347px; height: 30px;
    border-radius: 15px; background: var(--pink);
    display: flex; align-items: center; justify-content: center;
    color: var(--white); font-weight: 700; font-size: 19px;
  }
  .card--automation .phone {
    position: absolute; top: 622px; left: 28px;
    display: flex; align-items: center; gap: 6px;
    color: var(--white); font-weight: 700; font-size: 20px;
  }
</style>
</head>
<body>

  <section class="card card--repairs" aria-label="Electronic repairs side">
    <svg class="card__bg" viewBox="0 0 377 667" preserveAspectRatio="none" aria-hidden="true">
      <defs>
        <linearGradient id="repairsPink" x1="0" y1="0" x2="1" y2="1">
          <stop offset="0" stop-color="#f27dbb"/>
          <stop offset="1" stop-color="#e23f92"/>
        </linearGradient>
        <linearGradient id="repairsDark" x1="0" y1="0" x2="1" y2="0">
          <stop offset="0" stop-color="#1b1b1b"/>
          <stop offset="0.5" stop-color="#555"/>
          <stop offset="1" stop-color="#1b1b1b"/>
        </linearGradient>
      </defs>
      <polygon points="0,0 377,0 377,282 188,340 0,282" fill="url(#repairsPink)"/>
      <polygon points="0,282 188,340 377,282 377,308 188,362 0,308" fill="url(#repairsDark)"/>
      <polygon points="0,308 188,362 377,308 377,330 188,380 0,330" fill="#dcdcdc"/>
    </svg>
    <div class="logo">KIVORA</div>
    <div class="categories"><span>LAPTOPS</span><span>MOBILES</span><span>TABLETS</span></div>
    <div class="devices" role="img" aria-label="Group of devices: desktop monitor, tablets, phone, laptop and smart band"></div>
    <p class="tagline">FOR ANY REPAIRS, WE COME TO YOU,<br>WITH UNBEATABLE PRICES</p>
    <p class="headline">ALL ELECTRONIC REPAIRS</p>
    <div class="phone-pill">
      <svg width="16" height="20" viewBox="0 0 16 20" aria-hidden="true"><rect x="2" y="1" width="11" height="18" rx="2" fill="none" stroke="currentColor" stroke-width="2"/><rect x="6" y="15" width="3" height="2" fill="currentColor"/></svg>
      <span>(555) 214-3907</span>
    </div>
    <p class="email">
      <svg width="16" height="12" viewBox="0 0 16 12" aria-hidden="true"><rect x="1" y="1" width="14" height="10" fill="none" stroke="currentColor" stroke-width="1.5"/><path d="M1 1 L8 7 L15 1" fill="none" stroke="currentColor" stroke-width="1.5"/></svg>
      <span>Tech@Kivora.help</span>
    </p>
  </section>

  <section class="card card--automation" aria-label="Home automation side">
    <svg class="card__bg" viewBox="0 0 377 667" preserveAspectRatio="none" aria-hidden="true">
      <defs>
        <linearGradient id="autoDark" x1="0" y1="0" x2="1" y2="1">
          <stop offset="0" stop-color="#3a3a3a"/>
          <stop offset="1" stop-color="#111"/>
        </linearGradient>
        <linearGradient id="autoPink" x1="0" y1="0" x2="1" y2="1">
          <stop offset="0" stop-color="#d8358a"/>
          <stop offset="1" stop-color="#f07dba"/>
        </linearGradient>
      </defs>
      <rect width="377" height="667" fill="url(#autoDark)"/>
      <polygon points="0,498 188,560 377,498 377,524 188,588 0,524" fill="#e9e9e9"/>
      <polygon points="0,524 188,588 377,524 377,667 0,667" fill="url(#autoPink)"/>
    </svg>
    <div class="logo">KIVORA</div>
    <h2 class="section-title">HOME AUTOMATION</h2>
    <ul class="services">
      <li>Security Camera Installation</li>
      <li>Sink Installation</li>
      <li>Fireplace Mounting</li>
      <li>Chandelier Installation</li>
      <li>Television &amp; Sound Bar Mounting<span class="note">(Hidden Wires Optional)</span></li>
    </ul>
    <div class="feature-pill">PROFESSIONAL TV MOUNTING</div>
    <div class="phone">
      <svg width="16" height="20" viewBox="0 0 16 20" aria-hidden="true"><rect x="2" y="1" width="11" height="18" rx="2" fill="none" stroke="currentColor" stroke-width="2"/><rect x="6" y="15" width="3" height="2" fill="currentColor"/></svg>
      <span>(555) 214-3907</span>
    </div>
  </section>

</body>
</html>
```